Corvel Capital LLC

Need Professional Business cards for New Investment Fund

Target Market(s)

High Quality investors

Industry/Entity Type

Financial

Contact Information for Business Card

Phone Number +1 555 284 6190
Name Lukas Varenko
Title Fund Manager
email lv@FundCorvel.com
Website www.FundCorvel.com

Colors

Designer to choose colors to be used in the design.

Requirements
Must have
• Must have our Logo and all of the above. Must be made so lettering and loge can be raised

```html
<!DOCTYPE html>
<html lang="en">
<head>
<meta charset="utf-8">
<title>Velqor Capital – Business Card</title>
<link rel="stylesheet" href="https://fonts.googleapis.com/css2?family=Roboto:wght@400;500;700&display=swap">
<style>
  :root {
    --backdrop: #c6c6c6;
    --card-dark: #3a4540;
    --card-light: #f1f1f1;
    --ink: #343d39;
    --ink-soft: #3f4744;
    --accent: #8cc63f;
    --logo-light: #cfd2d0;
  }
  * { margin: 0; padding: 0; box-sizing: border-box; }
  html, body {
    width: 1200px; height: 1138px; overflow: hidden;
    background: var(--backdrop);
    font-family: "Roboto", Arial, sans-serif;
  }
  .canvas { position: relative; width: 1200px; height: 1138px; }

  .card {
    position: absolute;
    border-radius: 16px;
    overflow: hidden;
  }
  .card--front {
    left: 274px; top: 186px; width: 622px; height: 374px;
    background: var(--card-dark);
  }
  .card--back {
    left: 276px; top: 608px; width: 618px; height: 374px;
    background: var(--card-light);
  }

  .brand {
    position: absolute;
    display: flex; align-items: center; gap: 12px;
    font-weight: 500; letter-spacing: 1px;
    white-space: nowrap;
  }
  .brand__mark { display: block; flex: none; }
  .card--front .brand {
    left: 0; right: 0; top: 166px; justify-content: center;
    font-size: 62px; line-height: 62px; color: var(--logo-light);
  }
  .card--front .brand__mark { width: 22px; height: 22px; background: var(--logo-light); }
  .card--back .brand {
    left: 372px; top: 268px;
    font-size: 46px; line-height: 48px; color: var(--ink);
  }
  .card--back .brand__mark { width: 18px; height: 18px; background: var(--accent); }

  .accent-dot {
    position: absolute; left: -60px; top: 48px;
    width: 72px; height: 72px; border-radius: 50%;
    background: var(--accent);
  }
  .holder { position: absolute; left: 35px; top: 56px; color: var(--ink); }
  .holder__name { font-size: 26px; font-weight: 700; line-height: 30px; }
  .holder__title { font-size: 16px; font-weight: 400; line-height: 20px; margin-top: 5px; color: var(--ink-soft); }

  .contacts { position: absolute; left: 35px; top: 212px; list-style: none; color: var(--ink-soft); font-size: 16px; }
  .contacts li { display: flex; align-items: center; height: 23.5px; }
  .contacts svg { width: 14px; height: 14px; margin-left: 2px; margin-right: 16px; fill: var(--accent); }

  .address { position: absolute; left: 35px; top: 289px; color: var(--ink-soft); font-size: 16px; line-height: 24px; font-style: normal; }
</style>
</head>
<body>
<main class="canvas">
  <section class="card card--front" aria-label="Card front">
    <div class="brand"><span class="brand__mark"></span><span class="brand__name">VELQOR</span></div>
  </section>

  <section class="card card--back" aria-label="Card back">
    <span class="accent-dot"></span>
    <div class="holder">
      <p class="holder__name">Lukas Varenko</p>
      <p class="holder__title">Fund Manager</p>
    </div>
    <ul class="contacts">
      <li>
        <svg viewBox="0 0 16 16" aria-hidden="true"><path d="M2 6c0-2 2-3 6-3s6 1 6 3v1h-3V5.5H5V7H2zM4 8h8l2 6H2z"/></svg>
        +1 555 284 6190
      </li>
      <li>
        <svg viewBox="0 0 16 16" aria-hidden="true"><path d="M1 3h14v10H1zM2 4l6 5 6-5v1.4L8 10.4 2 5.4z" fill-rule="evenodd"/></svg>
        lv@FundCorvel.com
      </li>
      <li>
        <svg viewBox="0 0 16 16" aria-hidden="true"><path d="M8 1a7 7 0 1 0 0 14A7 7 0 0 0 8 1zm0 1.3c.8 0 1.7 1.5 2 4H6c.3-2.5 1.2-4 2-4zM2.4 7.3h2.4c0-1.6.3-3 .8-3.9A5.7 5.7 0 0 0 2.4 7.3zm8.8 0h2.4a5.7 5.7 0 0 0-3.2-3.9c.5.9.8 2.3.8 3.9zM6 8.7h4c-.3 2.5-1.2 4-2 4s-1.7-1.5-2-4zm-3.6 0a5.7 5.7 0 0 0 3.2 3.9c-.5-.9-.8-2.3-.8-3.9zm8.8 0c0 1.6-.3 3-.8 3.9a5.7 5.7 0 0 0 3.2-3.9z"/></svg>
        www.FundCorvel.com
      </li>
    </ul>
    <address class="address">48 Alder Row<br>Fairhaven, NJ, 08990</address>
    <div class="brand"><span class="brand__mark"></span><span class="brand__name">VELQOR</span></div>
  </section>
</main>
</body>
</html>
```